Update Powerpoint Presentation

We need to update the existing Powerpoint presentation to make it look more professional, less words and get the message across to potential clients. Our clients are banks and lenders in Australia.
Reason: To give the designers more time to come up with designs
Reason: I am looking for a design that is more innovative and doesn't just re-create what I gave. This presentation is only an example of what I would like I am keen to find a presentation that takes it to the next level.
It Professional

```html
<!DOCTYPE html>
<html lang="en">
<head>
<meta charset="utf-8">
<title>Northgate Presentation Slides</title>
<link href="https://fonts.googleapis.com/css2?family=Open+Sans:wght@400;600;700&family=Tinos:ital,wght@1,700&display=swap" rel="stylesheet">
<style>
  :root {
    --navy: #2b3990;
    --navy-deep: #1f2c7a;
    --cyan: #34ace0;
    --panel: #e9e9ea;
    --ink: #333333;
    --grey-text: #555659;
    --backdrop: #d9d6d0;
  }
  * { box-sizing: border-box; margin: 0; padding: 0; }
  html, body { width: 1200px; height: 606px; overflow: hidden; }
  body {
    background: var(--backdrop);
    font-family: "Open Sans", Arial, sans-serif;
    color: var(--ink);
    position: relative;
  }
  .slide {
    position: absolute;
    width: 380px;
    height: 286px;
    background: linear-gradient(180deg, #ffffff 0%, #f3f3f4 100%);
    box-shadow: 0 2px 6px rgba(0,0,0,0.25);
    overflow: hidden;
  }
  .slide--cover { left: 218px; top: 10px; }
  .slide--messages { left: 623px; top: 10px; }
  .slide--intro { left: 8px; top: 310px; }
  .slide--services { left: 414px; top: 310px; }
  .slide--closing { left: 812px; top: 310px; }

  .footer-band { position: absolute; left: 0; bottom: 0; width: 380px; height: 36px; }
  .footer-url {
    position: absolute; right: 40px; bottom: 6px;
    color: #fff; font-size: 9.5px; letter-spacing: 2px; font-weight: 600;
  }
  .confidential {
    position: absolute; left: 12px; top: 264px;
    font-size: 5px; font-weight: 600; color: var(--ink); letter-spacing: 0.2px;
  }

  .tag {
    position: absolute;
    background: var(--navy);
    color: #fff;
    border-radius: 6px 0 6px 6px;
    display: flex; align-items: center; justify-content: center;
    font-weight: 400;
    letter-spacing: 0.3px;
  }
  .tag::after {
    content: ""; position: absolute; right: -7px; top: 0;
    border-left: 8px solid var(--navy); border-bottom: 12px solid transparent;
  }

  .brand-name {
    position: absolute; color: var(--navy); font-weight: 700;
    line-height: 1; text-align: center; white-space: nowrap;
  }
  .brand-name--small { right: 14px; top: 16px; font-size: 20px; }
  .brand-name--large { left: 0; width: 380px; font-size: 58px; }

  /* Cover */
  .slide--cover .brand-name--large { top: 78px; }
  .slide--cover .tag { left: 124px; top: 168px; width: 146px; height: 23px; font-size: 13px; }
  .cover-client { position: absolute; left: 0; width: 380px; text-align: center; font-size: 10.5px; color: #222; }

  /* Key messages */
  .slide--messages .tag, .slide--intro .tag, .slide--services .tag { left: 12px; top: 16px; height: 23px; font-size: 12.5px; padding: 0 8px; }
  .msg-label {
    position: absolute; left: 11px; width: 72px;
    background: var(--navy); color: #fff; font-size: 7px; font-weight: 600;
    text-align: center; border-radius: 3px 0 3px 3px;
    display: flex; align-items: center; justify-content: center; line-height: 1.25;
  }
  .msg-label::after {
    content: ""; position: absolute; right: -5px; top: 0;
    border-left: 6px solid var(--navy); border-bottom: 8px solid transparent;
  }
  .msg-body {
    position: absolute; left: 99px; width: 262px;
    background: var(--cyan); color: #fff; border-radius: 4px;
    font-size: 4.4px; line-height: 1.35; padding: 3px 5px; overflow: hidden;
  }
  .msg-body b { font-weight: 700; }

  /* Introduction */
  .intro-heading { position: absolute; top: 62px; font-size: 8.5px; font-weight: 700; color: #111; }
  .intro-text {
    position: absolute; left: 8px; top: 82px; width: 177px; height: 172px;
    background: var(--navy); color: #fff; border-radius: 3px;
    font-size: 5.3px; line-height: 1.4; padding: 8px 8px;
  }
  .intro-text p + p { margin-top: 6px; }
  .offices-panel {
    position: absolute; left: 194px; top: 82px; width: 173px; height: 172px;
    background: var(--navy); border-radius: 3px; padding: 10px;
  }
  .offices-map {
    width: 100%; height: 100%;
    background: radial-gradient(ellipse at 60% 55%, #c99bc8 0%, #d3a9cf 45%, #f1dcc8 80%);
    border-radius: 30% 45% 40% 20%;
  }

  /* Services */
  .services-intro { position: absolute; left: 14px; top: 50px; width: 352px; font-size: 4.8px; line-height: 1.4; color: #222; }
  .services-note { position: absolute; left: 14px; top: 76px; font-size: 4.8px; color: #222; }
  .flow-side {
    position: absolute; left: 14px; width: 14px; background: var(--navy);
    color: #fff; font-size: 6.5px; font-style: italic;
    writing-mode: vertical-rl; transform: rotate(180deg);
    display: flex; align-items: center; justify-content: center; border-radius: 2px;
  }
  .flow-head, .flow-detail {
    position: absolute; left: 32px; width: 312px; display: grid;
  }
  .flow-head { background: var(--cyan); border-radius: 3px; }
  .flow-head span {
    font-size: 4.6px; font-style: italic; color: var(--navy-deep); text-align: center;
    display: flex; align-items: center; justify-content: center; line-height: 1.2;
    border-right: 1px solid rgba(255,255,255,0.7); padding: 0 2px;
  }
  .flow-head span:last-child { border-right: 0; }
  .flow-detail { background: var(--panel); border-radius: 2px; padding: 3px 0; overflow: hidden; }
  .flow-detail ul { list-style: none; font-size: 3.8px; line-height: 1.3; padding: 0 3px; color: #333; }
  .flow-detail li::before { content: "• "; }
  .grid-seven { grid-template-columns: repeat(7, 1fr); }
  .grid-six { grid-template-columns: repeat(6, 1fr); width: 296px; }

  /* Closing */
  .slide--closing .brand-name--large { top: 62px; }
  .thanks {
    position: absolute; left: 0; top: 152px; width: 380px; text-align: center;
    font-family: "Tinos", "Times New Roman", serif; font-style: italic; font-weight: 700;
    font-size: 22px; line-height: 1.05; color: var(--grey-text);
  }
  .contact { position: absolute; left: 0; width: 380px; text-align: center; font-size: 8.5px; color: #333; }
</style>
</head>
<body>

<svg width="0" height="0" style="position:absolute">
  <defs>
    <symbol id="footer-shape" viewBox="0 0 380 36">
      <path d="M0 26 H160 C175 26 180 14 196 14 H380 V22 H196 C182 22 176 30 160 30 H0 Z" fill="#34ace0"/>
      <path d="M0 29 H160 C176 29 182 18 198 18 H380 V36 H0 Z" fill="#2b3990"/>
    </symbol>
  </defs>
</svg>

<!-- Cover -->
<section class="slide slide--cover">
  <div class="brand-name brand-name--large">Northgate</div>
  <div class="tag">PRESENTATION TO</div>
  <p class="cover-client" style="top:213px">XYZ Lender</p>
  <p class="cover-client" style="top:234px">June 2013</p>
  <svg class="footer-band"><use href="#footer-shape"/></svg>
  <span class="footer-url">www.northgatels.com</span>
</section>

<!-- Key messages -->
<section class="slide slide--messages">
  <div class="tag">KEY MESSAGES</div>
  <div class="brand-name brand-name--small">Northgate</div>

  <div class="msg-label" style="top:64px;height:14px">XYZ Lender</div>
  <div class="msg-body" style="top:60px;height:22px">XYZ Lender currently outsources Mortgage Processing of New Loans and Discharges to a third party. XYZ Lender is looking to explore alternative models to enhance its existing service proposition through innovation and technology enhancements.</div>

  <div class="msg-label" style="top:102px;height:13px">NLS</div>
  <div class="msg-body" style="top:91px;height:37px">NLS is the largest outsource mortgage document and settlement business in Australia. Its ultimate parent, Harbourline Financial Group, is a leading global provider of title insurance and settlement services for residential and commercial real estate transactions. With revenues of approximately $3.8 billion in 2012, the company offers its products and services directly and through its agents and partners throughout the United States and abroad.</div>

  <div class="msg-label" style="top:160px;height:42px">Key<br>opportunities of<br>working with<br>NLS</div>
  <div class="msg-body" style="top:138px;height:90px">
    <b>Refinances</b> – NLS currently undertakes switching for other clients and is achieving take-up of between 50% and 70% with settlements occurring on day 1 from documents being returned. We would like to discuss opportunities for us to undertake the refinance process on behalf of XYZ Lender and work with your clients to ensure the best possible uptake.<br>
    <b>Electronic Documents and Web Signing</b> – NLS has deployed this technology in New Zealand to allow electronic delivery of documents and web signing, and is in discussions with other lenders in Australia. NLS would like to work with XYZ Lender in establishing an Electronic Document delivery solution.<br>
    <b>Discharges</b> – NLS would like to discuss the outsourcing of XYZ Lender's discharges to NLS. Relationship with the Third Party Channel – NLS has a strong relationship with all the major aggregator groups and understands their business, and can work closely with them by undertaking their own white label processing.<br>
    <b>NECH</b> – NLS is working closely with NECH to ensure a smooth transition from the existing manual processes to the new "Electronic World" of Conveyancing.
  </div>

  <div class="msg-label" style="top:236px;height:18px">Commitment<br>Sought</div>
  <div class="msg-body" style="top:239px;height:15px">NLS would like to work closely with XYZ Lender with a view to enhance XYZ Lender's end-to-end mortgage processing solution.</div>

  <span class="confidential">COMMERCIAL IN CONFIDENCE</span>
  <svg class="footer-band"><use href="#footer-shape"/></svg>
  <span class="footer-url">www.northgatels.com</span>
</section>

<!-- Introduction -->
<section class="slide slide--intro">
  <div class="tag">INTRODUCTION</div>
  <div class="brand-name brand-name--small">Northgate</div>
  <h2 class="intro-heading" style="left:16px">ABOUT NORTHGATE LENDING SERVICES</h2>
  <h2 class="intro-heading" style="left:199px">NLS OFFICES</h2>
  <div class="intro-text">
    <p>Northgate Lending Services (NLS) was established in NZ in 2001 and opened an office in Australia in 2004. In November 2007 NLS became a wholly owned subsidiary of Harbourline Financial Group and is the vehicle through which Harbourline undertakes mortgage servicing in Australia and New Zealand.</p>
    <p>On 1 August 2012 NLS acquired Summit Lenders Settlement Services (SLSS) to form one of the largest mortgage processing companies in Australasia.</p>
    <p>In providing services to the mortgage industry, NLS utilizes and deploys its existing resources and capability as well as the resources available to it through the Harbourline family of companies internationally.</p>
    <p>NLS have approximately 300 staff operating in offices in Sydney, Melbourne, Adelaide, Brisbane, Perth and Auckland, refer map opposite.</p>
    <p>NLS undertakes approximately 150,000 settlements p.a.</p>
  </div>
  <div class="offices-panel">
    <div class="offices-map" role="img" aria-label="Map of Australia and New Zealand marking office locations and staff numbers in Perth, Adelaide, Melbourne, Sydney, Brisbane and Auckland"></div>
  </div>
  <span class="confidential">COMMERCIAL IN CONFIDENCE</span>
  <svg class="footer-band"><use href="#footer-shape"/></svg>
  <span class="footer-url">www.northgatels.com</span>
</section>

<!-- Service offerings -->
<section class="slide slide--services">
  <div class="tag">SERVICE OFFERINGS</div>
  <div class="brand-name brand-name--small">Northgate</div>
  <p class="services-intro">"Mortgage Servicing" can mean different things in different jurisdictions. For the purpose of this document we use it to refer to the full range of mortgage management and administration services during the period from receipt of instructions to prepare documents until repayment and discharge of the mortgage that can be outsourced by the lender to a third party.</p>
  <p class="services-note">The diagram below details the services provided by NLS.</p>

  <div class="flow-side" style="top:86px;height:88px">New Loans</div>
  <div class="flow-head grid-seven" style="top:86px;height:21px">
    <span>Document Preparation</span><span>Verification</span><span>Bookings And Enquiries</span><span>Certification &amp; Settlement Preparation</span><span>Settlements</span><span>Stamping And Lodgement</span><span>Custody</span>
  </div>
  <div class="flow-detail grid-seven" style="top:110px;height:64px">
    <ul><li>File creation</li><li>Complete / check title search</li><li>Check fees</li><li>Produce loan document pack</li><li>Forward documents to borrower</li></ul>
    <ul><li>Verify that executed documents are completed correctly signed and witnessed</li><li>Follow up on incomplete documents</li></ul>
    <ul><li>Contact the solicitor / conveyancer to book settlement</li><li>Contact outgoing lender to book settlement</li><li>Book settlement in settlement diary</li></ul>
    <ul><li>Send certification document to lender and request funds</li><li>Confirm funds and disbursements required at settlement</li><li>Issue cheques</li></ul>
    <ul><li>Complete final search</li><li>Collect bank cheques for settlement</li><li>Attend settlement</li><li>Confirm settlement and attend post settlement activities</li></ul>
    <ul><li>Stamping of documents</li><li>Lodgement of the documents with the relevant LTO</li></ul>
    <ul><li>Registered documents returned from LTO</li><li>Trail documents to the custodian</li></ul>
  </div>

  <div class="flow-side" style="top:179px;height:79px">Discharges</div>
  <div class="flow-head grid-six" style="top:179px;height:22px">
    <span>Document preparation</span><span>Bookings and enquiries</span><span>Advise payout figures</span><span>Prepare settlement instructions</span><span>Settlements</span><span>Custody</span>
  </div>
  <div class="flow-detail grid-six" style="top:205px;height:53px">
    <ul><li>File creation</li><li>Check fees</li><li>Produce discharge documents and arrange execution by attorney</li><li>Forward letter to requesting party</li></ul>
    <ul><li>Book settlement in the settlement diary</li></ul>
    <ul><li>Receive the payout figure from the outgoing lender</li><li>Advise payout figure and any fees to the incoming lender</li></ul>
    <ul><li>Forward discharge documents and settlement instructions to effect settlement to applicable state office or settlement agent</li></ul>
    <ul><li>Attend settlement and collect funds to payout loan</li><li>Deposit cheques</li></ul>
    <ul><li>Trail any remaining documents from the security packet to the custodian</li></ul>
  </div>

  <span class="confidential">COMMERCIAL IN CONFIDENCE</span>
  <svg class="footer-band"><use href="#footer-shape"/></svg>
  <span class="footer-url">www.northgatels.com</span>
</section>

<!-- Closing -->
<section class="slide slide--closing">
  <div class="brand-name brand-name--large">Northgate</div>
  <p class="thanks">Thank You<br>For Your Attention</p>
  <p class="contact" style="top:212px">T: 123-456-0789</p>
  <p class="contact" style="top:226px">Street Name, City Name, State Zip Code</p>
  <svg class="footer-band"><use href="#footer-shape"/></svg>
  <span class="footer-url">www.northgatels.com</span>
</section>

</body>
</html>
```